Business card design needed

I would like a one sided black business card with the information provided above. Refer to my website www.brightvolleyracquets.com.au for an example of colors I have used for my site, would like to keep this consistent for my business cards also, I will upload my logo below.

I am a new small business that provides tennis customers with racquet re stringing, tennis strings and accessories.

Industry/Entity Type

Small Business

Contact Information for Business Card

Bright Volley Tennis

Owen Whitby
Managing Director

brightvolleyracquets@mailbox.example
www.brightvolleyracquets.com.au
0491 726 305

Racquet Restringing/Tennis Strings/Accessories

Requirements
Must have
• Must have my logo and card must be black

```html
<!DOCTYPE html>
<html lang="en">
<head>
<meta charset="utf-8">
<title>Bright Volley Tennis – Business Card</title>
<link rel="stylesheet" href="https://fonts.googleapis.com/css2?family=Open+Sans:wght@400;600;700&display=swap">
<style>
  :root {
    --page-bg: #e8e5e0;
    --card-black: #050505;
    --lime: #b6d433;
    --court-blue: #1f4f8f;
    --text-white: #ffffff;
    --text-dark: #1a1a1a;
    --font-main: "Open Sans", Arial, sans-serif;
  }
  * { margin: 0; padding: 0; box-sizing: border-box; }
  html, body {
    width: 1200px;
    height: 750px;
    overflow: hidden;
    background: var(--page-bg);
    font-family: var(--font-main);
  }
  .business-card {
    position: absolute;
    left: 75px;
    top: 75px;
    width: 1050px;
    height: 600px;
    border-radius: 36px;
    background: var(--card-black);
    overflow: hidden;
  }
  .brand {
    position: absolute;
    left: 0;
    top: 200px;
    width: 100%;
    display: flex;
    justify-content: center;
    align-items: center;
    gap: 22px;
  }
  .brand-dot {
    width: 58px;
    height: 58px;
    border-radius: 50%;
    background: var(--lime);
  }
  .brand-name {
    color: var(--lime);
    font-size: 60px;
    font-weight: 700;
    letter-spacing: 1px;
    line-height: 1;
  }
  .contact-list {
    position: absolute;
    left: 72px;
    top: 362px;
    list-style: none;
  }
  .contact-item {
    display: flex;
    align-items: center;
    height: 44px;
    color: var(--text-white);
    font-size: 24px;
  }
  .contact-icon {
    width: 22px;
    height: 22px;
    margin-right: 11px;
    flex: none;
  }
  .services-list {
    position: absolute;
    left: 612px;
    top: 356px;
    list-style: none;
  }
  .service-item {
    display: flex;
    align-items: center;
    height: 45px;
    color: var(--text-white);
    font-size: 32px;
  }
  .service-item::before {
    content: "";
    width: 9px;
    height: 9px;
    background: var(--text-white);
    margin-right: 13px;
    flex: none;
  }
  .footer-band {
    position: absolute;
    left: 0;
    top: 0;
    width: 1050px;
    height: 600px;
  }
  .signature {
    position: absolute;
    left: 0;
    top: 545px;
    width: 100%;
    text-align: center;
    color: var(--text-dark);
    font-size: 23px;
  }
  .signature-name {
    font-weight: 700;
    font-size: 27px;
  }
</style>
</head>
<body>
  <article class="business-card">
    <div class="brand">
      <span class="brand-dot"></span>
      <span class="brand-name">Bright Volley Tennis</span>
    </div>

    <ul class="contact-list">
      <li class="contact-item">
        <svg class="contact-icon" viewBox="0 0 24 24" aria-hidden="true">
          <path fill="var(--lime)" d="M3 9c0-3 4-5 9-5s9 2 9 5v2h-5V9c-1-1-7-1-8 0v2H3z"/>
          <path fill="var(--lime)" d="M7 12l2-2h6l2 2 3 4v4H4v-4z"/>
          <circle cx="12" cy="16" r="2.2" fill="var(--card-black)"/>
        </svg>
        0491 726 305
      </li>
      <li class="contact-item">
        <svg class="contact-icon" viewBox="0 0 24 24" aria-hidden="true">
          <rect x="2" y="5" width="20" height="14" rx="1.5" fill="var(--lime)"/>
          <path d="M2.5 6l9.5 7 9.5-7" fill="none" stroke="var(--card-black)" stroke-width="1.6"/>
        </svg>
        brightvolleyracquets@mailbox.example
      </li>
      <li class="contact-item">
        <svg class="contact-icon" viewBox="0 0 24 24" aria-hidden="true">
          <circle cx="12" cy="12" r="10" fill="var(--lime)"/>
          <g fill="none" stroke="var(--card-black)" stroke-width="1.3">
            <ellipse cx="12" cy="12" rx="4.5" ry="10"/>
            <path d="M2 12h20M4 7h16M4 17h16"/>
          </g>
        </svg>
        www.brightvolleyracquets.com.au
      </li>
    </ul>

    <ul class="services-list">
      <li class="service-item">Racquet Restringing</li>
      <li class="service-item">Tennis Strings</li>
      <li class="service-item">Accessories</li>
    </ul>

    <svg class="footer-band" viewBox="0 0 1050 600" aria-hidden="true">
      <path d="M0 544 Q525 484 1050 544" fill="none" stroke="var(--court-blue)" stroke-width="5"/>
      <path d="M0 551 Q525 491 1050 551 L1050 600 L0 600 Z" fill="var(--lime)"/>
    </svg>

    <p class="signature"><span class="signature-name">Owen Whitby,</span> Managing Director</p>
  </article>
</body>
</html>
```